WebApp for IoT (Vexa lights and Kirra/Brelline)

I am going to create my own dashbord for Quillet Pro (See other examples on https://quillet.example/) But I want it much more flexible and advanced.
One page per room (So I can have an Zanbo in each room with all functions just for that room) and include controls for light (both overall for the room and in an popupwindow all lightbulbs n the room - se more about how its done in Torvald Vexa app on https://www.torvald-vexa.example/en-us/explore-vexa/apps/bridge) aswell as set volume/track for Kirra.

I want the final solution to be "skinable" so I can choose from Blue-CSS to Green-CSS etc, but at this moment I only want ONE color!

I have added an PDF with the functions I am thinking of, but the design is for you to create!

Please have in mind it will be running on Zanbos on the wall, and in the mobile.

For the moment I only want an PSD of the "Room page", "Light popup" and "Sound Popup", but I might contract the winner to get HTML/CSS as second step.

```html
<!DOCTYPE html>
<html lang="en">
<head>
<meta charset="utf-8">
<title>Room Pages – Kitchen &amp; Bedroom</title>
<link rel="stylesheet" href="https://fonts.googleapis.com/css2?family=Manrope:wght@500;600;700&display=swap">
<style>
  :root {
    --page-bg: #165bd8;
    --screen-bg: #3a3633;
    --accent-green: #5cb22a;
    --accent-blue: #1658d4;
    --text-light: #ffffff;
    --slider-top: #1d1d1d;
    --slider-bottom: #3b3b3b;
    --icon-green: #5cb22a;
    --icon-blue: #1658d4;
  }
  * { box-sizing: border-box; margin: 0; padding: 0; }
  html, body { width: 842px; height: 1200px; overflow: hidden; }
  body {
    background: var(--page-bg);
    font-family: "Manrope", sans-serif;
    color: var(--text-light);
    position: relative;
  }
  .room-screen {
    position: absolute;
    left: 73px;
    width: 695px;
    height: 490px;
    border-radius: 16px;
    overflow: hidden;
    background: var(--screen-bg);
  }
  .room-screen--kitchen { top: 69px; }
  .room-screen--bedroom { top: 641px; }
  .room-photo { position: absolute; inset: 0; }
  .room-photo--kitchen {
    background:
      radial-gradient(ellipse at 60% 75%, rgba(120,100,80,.35), transparent 60%),
      linear-gradient(180deg, #4a4745 0%, #3f3d3b 45%, #2e2a27 100%);
  }
  .room-photo--bedroom {
    background:
      radial-gradient(ellipse at 60% 80%, rgba(140,130,120,.35), transparent 60%),
      linear-gradient(90deg, #3d3733 0%, #4a4542 40%, #4d4a48 100%);
  }
  .room-title {
    position: absolute; left: 18px; top: 29px;
    font-size: 19px; font-weight: 600; letter-spacing: .3px;
  }
  .weather {
    position: absolute; left: 297px; width: 100px; top: 27px;
    text-align: center; line-height: 1.15;
  }
  .weather__temp { font-size: 22px; font-weight: 600; }
  .weather__state { font-size: 17.5px; font-weight: 500; }
  .clock {
    position: absolute; left: 588px; width: 80px; top: 26px;
    text-align: center; font-size: 13px; font-weight: 500; line-height: 1.5;
  }
  .control-btn {
    position: absolute;
    width: 133px; height: 42px;
    border: 2px solid var(--text-light);
    border-radius: 21px;
    display: flex; align-items: center;
    padding-left: 2px;
    font-size: 12.5px; font-weight: 600;
  }
  .control-btn--green { background: var(--accent-green); }
  .control-btn--blue { background: var(--accent-blue); }
  .control-btn__icon {
    width: 34px; height: 34px; border-radius: 50%;
    background: var(--text-light);
    display: flex; align-items: center; justify-content: center;
    margin-right: 10px; flex-shrink: 0;
  }
  .control-btn--volume .control-btn__label { margin-left: 3px; }
  .left-col { left: 25px; }
  .right-col { left: 537px; }
  .brightness {
    position: absolute; left: 176px; top: 198px;
    width: 50px; height: 101px; border-radius: 14px; overflow: hidden;
    background: var(--slider-bottom);
  }
  .brightness__level {
    height: 51px; background: var(--slider-top);
    display: flex; align-items: center; justify-content: center;
    font-size: 12px; font-weight: 600;
  }
  .brightness__icon { display: flex; justify-content: center; padding-top: 14px; }
</style>
</head>
<body>

<svg width="0" height="0" style="position:absolute">
  <defs>
    <symbol id="icon-bulb" viewBox="0 0 24 24">
      <path d="M12 3a6 6 0 0 0-3.5 10.9V16h7v-2.1A6 6 0 0 0 12 3z" fill="none" stroke="currentColor" stroke-width="1.8"/>
      <path d="M12 9v4M10 10.5l2 1.5 2-1.5" fill="none" stroke="currentColor" stroke-width="1.4"/>
      <rect x="9" y="17.5" width="6" height="3.5" rx="1" fill="currentColor"/>
    </symbol>
    <symbol id="icon-speaker" viewBox="0 0 24 24">
      <path d="M4 9h4l5-4v14l-5-4H4z" fill="currentColor"/>
      <path d="M16 9.5a3.5 3.5 0 0 1 0 5" fill="none" stroke="currentColor" stroke-width="1.8"/>
    </symbol>
    <symbol id="icon-sun" viewBox="0 0 24 24">
      <circle cx="12" cy="12" r="5" fill="none" stroke="currentColor" stroke-width="1.2"/>
      <path d="M12 2v3M12 19v3M2 12h3M19 12h3M4.9 4.9l2.1 2.1M17 17l2.1 2.1M4.9 19.1 7 17M17 7l2.1-2.1" stroke="currentColor" stroke-width="1.2"/>
    </symbol>
  </defs>
</svg>

<section class="room-screen room-screen--kitchen">
  <div class="room-photo room-photo--kitchen" role="img" aria-label="Dimmed photo of a modern kitchen with island, bar stools and pendant lamps"></div>
  <h1 class="room-title">KITCHEN</h1>
  <div class="weather"><div class="weather__temp">25°C</div><div class="weather__state">SUNNY</div></div>
  <div class="clock">10:52PM<br>16-07-2022</div>

  <div class="control-btn control-btn--green left-col" style="top:198px">
    <span class="control-btn__icon" style="color:var(--icon-green)"><svg width="20" height="20"><use href="#icon-bulb"/></svg></span>
    <span class="control-btn__label">Light Details</span>
  </div>
  <div class="control-btn control-btn--blue left-col" style="top:260px">
    <span class="control-btn__icon" style="color:var(--icon-blue)"><svg width="20" height="20"><use href="#icon-bulb"/></svg></span>
    <span class="control-btn__label">Light</span>
  </div>
  <div class="brightness">
    <div class="brightness__level">65%</div>
    <div class="brightness__icon"><svg width="18" height="18"><use href="#icon-sun"/></svg></div>
  </div>

  <div class="control-btn control-btn--green right-col" style="top:211px">
    <span class="control-btn__icon" style="color:var(--icon-green)"><svg width="20" height="20"><use href="#icon-bulb"/></svg></span>
    <span class="control-btn__label">Light 01</span>
  </div>
  <div class="control-btn control-btn--green right-col" style="top:263px">
    <span class="control-btn__icon" style="color:var(--icon-green)"><svg width="20" height="20"><use href="#icon-bulb"/></svg></span>
    <span class="control-btn__label">Light 02</span>
  </div>
  <div class="control-btn control-btn--green right-col" style="top:316px">
    <span class="control-btn__icon" style="color:var(--icon-green)"><svg width="20" height="20"><use href="#icon-bulb"/></svg></span>
    <span class="control-btn__label">Light 03</span>
  </div>
</section>

<section class="room-screen room-screen--bedroom">
  <div class="room-photo room-photo--bedroom" role="img" aria-label="Dimmed photo of a bedroom with a grey upholstered bed and slatted wall"></div>
  <h1 class="room-title">BEDROOM</h1>
  <div class="weather"><div class="weather__temp">25°C</div><div class="weather__state">SUNNY</div></div>
  <div class="clock">10:52PM<br>16-07-2022</div>

  <div class="control-btn control-btn--green left-col" style="top:198px">
    <span class="control-btn__icon" style="color:var(--icon-green)"><svg width="20" height="20"><use href="#icon-bulb"/></svg></span>
    <span class="control-btn__label">Light Details</span>
  </div>
  <div class="control-btn control-btn--blue left-col" style="top:260px">
    <span class="control-btn__icon" style="color:var(--icon-blue)"><svg width="20" height="20"><use href="#icon-bulb"/></svg></span>
    <span class="control-btn__label">Light</span>
  </div>
  <div class="control-btn control-btn--green control-btn--volume left-col" style="top:316px">
    <span class="control-btn__icon" style="color:var(--icon-green)"><svg width="18" height="18"><use href="#icon-speaker"/></svg></span>
    <span class="control-btn__label">Volume</span>
  </div>
  <div class="brightness">
    <div class="brightness__level">65%</div>
    <div class="brightness__icon"><svg width="18" height="18"><use href="#icon-sun"/></svg></div>
  </div>

  <div class="control-btn control-btn--green right-col" style="top:211px">
    <span class="control-btn__icon" style="color:var(--icon-green)"><svg width="20" height="20"><use href="#icon-bulb"/></svg></span>
    <span class="control-btn__label">Light 01</span>
  </div>
  <div class="control-btn control-btn--green right-col" style="top:263px">
    <span class="control-btn__icon" style="color:var(--icon-green)"><svg width="20" height="20"><use href="#icon-bulb"/></svg></span>
    <span class="control-btn__label">Light 02</span>
  </div>
  <div class="control-btn control-btn--green right-col" style="top:316px">
    <span class="control-btn__icon" style="color:var(--icon-green)"><svg width="20" height="20"><use href="#icon-bulb"/></svg></span>
    <span class="control-btn__label">Light 03</span>
  </div>
  <div class="control-btn control-btn--green right-col" style="top:368px">
    <span class="control-btn__icon" style="color:var(--icon-green)"><svg width="20" height="20"><use href="#icon-bulb"/></svg></span>
    <span class="control-btn__label">Light 04</span>
  </div>
</section>

</body>
</html>
```